Business Card Design for company

We want new business cards. We'd like something different-- yet still highly professional. Our tagline is Providing leadership, delivering success. Stock photos are ok, as long as they are relevant and look upscale.

Target Market(s)

Architecture/Business Management Consulting/Engineering Consulting

Contact Information for Business Card

dark gray background with pops of blue might be good, but you tell me. You're the designers. Rounded corners might be nice, but again, you tell me.

Font styles to use
Serif
Sans Serif

Colors
3276b5
5c5c5c
9d9d9d
fbfbfb

Requirements
Nice to have
• Something different, but still very professional.

```html
<!DOCTYPE html>
<html lang="en">
<head>
<meta charset="utf-8">
<title>Halvern Group – Business Card</title>
<link rel="stylesheet" href="https://fonts.googleapis.com/css2?family=Roboto:wght@400;500;700&display=swap">
<style>
  :root {
    --blue: #3276b5;
    --blue-deep: #2a66a0;
    --gray-dark: #5c5c5c;
    --gray-mid: #9d9d9d;
    --paper: #fbfbfb;
    --slate: #4a4e55;
    --backdrop: #e4e5e7;
  }
  * { box-sizing: border-box; margin: 0; padding: 0; }
  html, body {
    width: 1200px; height: 768px; overflow: hidden;
    background: var(--backdrop);
    font-family: "Roboto", Arial, sans-serif;
  }
  .sheet {
    width: 1200px; height: 768px;
    display: flex; align-items: center; justify-content: center; gap: 40px;
  }
  .card {
    width: 560px; height: 320px;
    position: relative; overflow: hidden;
    box-shadow: 0 6px 18px rgba(0,0,0,0.18);
  }

  /* Back */
  .card-back {
    background: var(--slate);
    color: var(--paper);
    display: flex; flex-direction: column; align-items: center; justify-content: center;
  }
  .back-name {
    font-weight: 700; font-size: 58px; letter-spacing: 2px; line-height: 1;
    text-transform: uppercase;
  }
  .back-tagline {
    margin-top: 70px; font-size: 15px; letter-spacing: 0.5px;
  }

  /* Front */
  .card-front { background: var(--paper); }
  .front-brand {
    position: absolute; left: 34px; top: 82px; width: 230px;
    color: var(--blue);
    font-weight: 700; font-size: 44px; line-height: 1.05; letter-spacing: 1px;
    text-transform: uppercase;
  }
  .divider {
    position: absolute; left: 282px; top: 62px;
    width: 1px; height: 176px; background: var(--gray-mid);
  }
  .contact {
    position: absolute; left: 304px; top: 56px; width: 240px;
    color: var(--gray-dark);
  }
  .contact-name {
    color: var(--blue); font-weight: 700; font-size: 21px; letter-spacing: 0.5px;
    text-transform: uppercase; line-height: 1;
  }
  .contact-title {
    font-weight: 500; font-size: 13px; text-transform: uppercase; margin-top: 3px;
  }
  .contact-address { font-size: 13px; line-height: 1.3; margin-top: 8px; }
  .contact-lines { list-style: none; margin-top: 8px; font-size: 13px; line-height: 1.45; }
  .contact-lines li { display: flex; align-items: center; gap: 7px; }
  .contact-lines svg { width: 12px; height: 12px; fill: var(--blue); flex: none; }
  .web-band {
    position: absolute; right: 0; bottom: 0; width: 330px; height: 50px;
  }
  .web-band svg { position: absolute; inset: 0; }
  .web-address {
    position: absolute; right: 22px; bottom: 15px;
    color: var(--paper); font-size: 17px; letter-spacing: 0.3px;
  }
</style>
</head>
<body>
<main class="sheet">
  <section class="card card-back">
    <div class="back-name">Halvern Group</div>
    <p class="back-tagline">Providing leadership, delivering success.</p>
  </section>

  <section class="card card-front">
    <div class="front-brand">Halvern<br>Group</div>
    <div class="divider"></div>
    <div class="contact">
      <div class="contact-name">Daniel Reyes</div>
      <div class="contact-title">CEO/Founder</div>
      <p class="contact-address">2140 Birchwood Avenue<br>Juneau, Alaska 99801</p>
      <ul class="contact-lines">
        <li><svg viewBox="0 0 24 24" aria-hidden="true"><path d="M6.6 10.8a15.2 15.2 0 0 0 6.6 6.6l2.2-2.2a1 1 0 0 1 1-.25 11.4 11.4 0 0 0 3.6.6 1 1 0 0 1 1 1V20a1 1 0 0 1-1 1A17 17 0 0 1 3 4a1 1 0 0 1 1-1h3.5a1 1 0 0 1 1 1c0 1.25.2 2.45.6 3.6a1 1 0 0 1-.25 1z"/></svg>555 014 2290</li>
        <li><svg viewBox="0 0 24 24" aria-hidden="true"><path d="M7 1h10a2 2 0 0 1 2 2v18a2 2 0 0 1-2 2H7a2 2 0 0 1-2-2V3a2 2 0 0 1 2-2zm0 3v14h10V4z"/></svg>555 017 6083</li>
        <li><svg viewBox="0 0 24 24" aria-hidden="true"><path d="M6 2h12v6H6zM3 9h18a1 1 0 0 1 1 1v8h-4v4H6v-4H2v-8a1 1 0 0 1 1-1zm5 7v4h8v-4z"/></svg>555 019 4471</li>
        <li><svg viewBox="0 0 24 24" aria-hidden="true"><path d="M2 5h20v14H2zm2 2v.5l8 5.5 8-5.5V7zm0 3v7h16v-7l-8 5.5z"/></svg>daniel@halverngroup.com</li>
      </ul>
    </div>
    <div class="web-band">
      <svg viewBox="0 0 330 50" width="330" height="50" preserveAspectRatio="none" aria-hidden="true">
        <polygon points="0,50 40,0 330,0 330,50" fill="var(--blue-deep)"/>
      </svg>
      <span class="web-address">www.halverngroup.com</span>
    </div>
  </section>
</main>
</body>
</html>
```